Fast quick flyer for Merchant Growth Fair

I am an information security consultant that needs to have a flyer and QUICK!!!
I need to get it to the printer today to have if done by monday. Quick turnaound.
I don't need the most amazing flyer but something that will capture their attention and offer them 40% off my base rate.
Updates

Here's some slight updates to the text, can you update and incorporate (PS: For some reason, when I initially put in Vantrel Systems, a " (quote) showed up, it's an apostrophe ( Vantrel Systems): Text: Vantrel Systems is the information security department for small and mid-sized businesses. Leveraging our 20+ years of information security experience, we will bring you the same level of service found at Pinnacle 300 companies. Small and mid-sized companies are often the target of malicious activity because they tend to lack the expertise to properly secure their environments. Now you can have your very own information security department at a fraction of the cost of a full time staff. Our typical rate for our premium offering: Guardline Plus is $5000/month based on a signed one year commitment. But for expo attendees, we are offering a special discount. As an expo attendee, you are eligible for a 40% discount. Guardline Plus for expo attendees will be $3000/month based on a signed one year commitment. Why put your company and your business at risk. Vantrel Systems is here to secure your company's future! Contact us now for more information: Leon Whitcombe Vantrel Systems "The information security department of small and mid-sized companies" 555-318-7292 info@vantrelsys.example http://www.vantrelsys.example

Also, this is going to be a 6x9 heavy stock postcard

Addition: Promo Code: GrowthFair 2014

Target Market(s)

Small businesses with a small IT department that can't afford to hire a full time IT Security Staff. We are the outsourced Information Security group

Industry/Entity Type

Small Business

Colors

Designer to choose colors to be used in the design.

Requirements
Must have
• Sell the idea that they need to take security serious and that we are the ones to do the job

Should stress that because they are attendees of the Merchant Growth Fair, they are eligible to get a 40% discount on our standard rate

```html
<!DOCTYPE html>
<html lang="en">
<head>
<meta charset="utf-8">
<title>Vantrel Systems – Merchant Growth Fair Flyer</title>
<link rel="stylesheet" href="https://fonts.googleapis.com/css2?family=Arimo:wght@400;700&family=Roboto:wght@300;400;700;900&family=Roboto+Condensed:wght@700&display=swap">
<style>
  :root {
    --navy: #1f2a4d;
    --cyan: #1aa3e0;
    --slate: #58585a;
    --ink: #1e1e1e;
    --white: #ffffff;
    --photo-a: #c9ccd1;
    --photo-b: #8d97a5;
  }
  * { box-sizing: border-box; margin: 0; padding: 0; }
  html, body { width: 927px; height: 1200px; overflow: hidden; background: var(--white); }
  body { font-family: "Arimo", Arial, sans-serif; color: var(--ink); }
  .flyer { position: relative; width: 927px; height: 1200px; overflow: hidden; }

  .masthead { position: absolute; left: 0; top: 0; width: 927px; height: 183px; background: var(--navy); }
  .headline {
    position: absolute; left: 46px; top: 57px; color: var(--white);
    font-family: "Roboto", Arial, sans-serif;
    font-weight: 300; font-size: 56px; line-height: 55px; letter-spacing: -0.6px;
    text-shadow: 2px 2px 3px rgba(0,0,0,.45);
  }
  .headline strong { color: var(--cyan); font-weight: 900; }

  .badge {
    position: absolute; left: 718px; top: 48px; width: 164px; height: 150px;
    background: var(--white); border-radius: 10px; transform: rotate(13deg);
    display: flex; align-items: center; justify-content: center;
  }
  .badge-inner {
    width: 148px; height: 134px; background: var(--cyan); border-radius: 6px;
    color: var(--white); text-align: center; font-family: "Arimo", Arial, sans-serif;
    font-weight: 700; line-height: 1; padding-top: 6px;
  }
  .badge-pct { font-size: 56px; letter-spacing: -1px; }
  .badge-label { font-size: 19px; line-height: 18px; }

  .tile { position: absolute; width: 214px; height: 215px; }
  .tile-text {
    display: flex; flex-direction: column; align-items: center; justify-content: center;
    color: var(--white); font-size: 21px; line-height: 33px; text-align: center; font-weight: 400;
  }
  .tile-text strong { font-weight: 700; }
  .tile-slate { background: var(--slate); }
  .tile-navy { background: var(--navy); }
  .tile-photo { background: linear-gradient(135deg, var(--photo-a), var(--photo-b)); }
  .tile-photo.cool { background: linear-gradient(135deg, #b8c6d3, #4d6279); }
  .tile-photo.warm { background: linear-gradient(135deg, #eeeeee, #a9a39d); }

  .section-title { position: absolute; color: var(--cyan); font-family: "Arimo", Arial, sans-serif; font-weight: 700; font-size: 25px; }
  .body-copy { position: absolute; font-size: 15.5px; line-height: 23px; color: var(--ink); }

  .list { position: absolute; list-style: none; font-size: 14.5px; }
  .list li { display: flex; align-items: flex-start; gap: 8px; }
  .list svg { flex: none; width: 13px; height: 13px; margin-top: 3px; }
  .list-courses li { height: 25px; }
  .list-consulting li { margin-bottom: 8px; line-height: 17px; }
  .note { display: block; padding-left: 4px; }

  .callout {
    position: absolute; left: 754px; top: 532px; width: 114px; height: 114px; border-radius: 50%;
    background: var(--slate); color: var(--white); font-weight: 700; font-size: 13.5px; line-height: 17px;
    display: flex; align-items: center; justify-content: center; text-align: center;
  }

  .offer-title { position: absolute; left: 38px; top: 921px; color: var(--cyan); font-size: 29px; line-height: 34px; font-weight: 400; }
  .offer-list { position: absolute; left: 40px; top: 1000px; list-style: none; font-size: 14.5px; line-height: 24px; }
  .offer-list li { position: relative; padding-left: 18px; }
  .offer-list li::before { content: ""; position: absolute; left: 0; top: 7px; width: 10px; height: 10px; background: var(--cyan); }
  .offer-list .highlight { color: var(--cyan); font-weight: 700; }
  .offer-list .rate { display: block; color: var(--cyan); font-weight: 700; }

  .brand { position: absolute; left: 566px; top: 985px; display: flex; align-items: center; gap: 14px; }
  .brand-mark { width: 58px; height: 58px; background: var(--navy); }
  .brand-name { color: var(--navy); font-size: 34px; font-weight: 400; line-height: 36px; letter-spacing: 1px; }

  .footer { position: absolute; left: 0; top: 1095px; width: 927px; height: 105px; background: var(--slate); color: var(--white); font-family: "Roboto Condensed", Arial, sans-serif; font-weight: 700; }
  .contact-name { position: absolute; left: 46px; top: 31px; font-size: 22px; }
  .contact-role { position: absolute; left: 46px; top: 61px; font-size: 13px; }
  .divider { position: absolute; top: 30px; width: 2px; height: 48px; background: var(--white); }
  .phone { position: absolute; left: 300px; top: 26px; font-size: 27px; display: flex; gap: 8px; align-items: center; }
  .email { position: absolute; left: 302px; top: 61px; font-size: 15.5px; display: flex; gap: 9px; align-items: center; }
  .web { position: absolute; left: 612px; top: 35px; font-size: 29px; }
</style>
</head>
<body>
<svg width="0" height="0" style="position:absolute" aria-hidden="true">
  <symbol id="icon-arrow" viewBox="0 0 14 14">
    <circle cx="7" cy="7" r="6" fill="none" stroke="#1aa3e0" stroke-width="1.8"/>
    <path d="M4 7h5M7 4.5L9.5 7 7 9.5" fill="none" stroke="#1aa3e0" stroke-width="1.8" stroke-linecap="round" stroke-linejoin="round"/>
  </symbol>
</svg>

<main class="flyer">
  <header class="masthead">
    <h1 class="headline"><strong>SECURING</strong> THE FUTURE<br>OF YOUR COMPANY</h1>
    <div class="badge">
      <div class="badge-inner">
        <div class="badge-pct">40%</div>
        <div class="badge-label">DISCOUNT<br>FOR EXPO<br>ATTENDEES</div>
      </div>
    </div>
  </header>

  <div class="tile tile-slate tile-text" style="left:37px;top:211px"><strong>SECURITY</strong><span>CERTIFICATION</span><span>COURSES</span></div>
  <div class="tile tile-photo warm" style="left:264px;top:211px" role="img" aria-label="Photo: hands holding a tablet showing padlock icons over code"></div>
  <div class="tile tile-photo cool" style="left:37px;top:443px" role="img" aria-label="Photo: businessman touching a digital padlock over circuit lines"></div>
  <div class="tile tile-navy tile-text" style="left:264px;top:443px"><span>INFORMATION</span><strong>SECURITY</strong><span>CONSULTING</span></div>
  <div class="tile tile-slate tile-text" style="left:37px;top:675px"><strong>SECURITY</strong><span>CONFERENCES</span></div>
  <div class="tile tile-photo" style="left:264px;top:675px" role="img" aria-label="Photo: business team in a conference meeting"></div>

  <h2 class="section-title" style="left:505px;top:212px">ABOUT US</h2>
  <p class="body-copy" style="left:510px;top:248px;width:362px">Vantrel Systems as a information security department for small and mid-sized businesses.</p>
  <p class="body-copy" style="left:510px;top:317px;width:362px">Small companies are targets because they lack the expertise at information security that large companies have.&nbsp; We have over 20 years of information security experience and we can leverage our expertise to give small companies the same level of security experience that Pinnacle 300 companies have.</p>

  <h2 class="section-title" style="left:515px;top:498px">TRAINING COURSES</h2>
  <ul class="list list-courses" style="left:515px;top:535px">
    <li><svg><use href="#icon-arrow"/></svg>Core Security Pro</li>
    <li><svg><use href="#icon-arrow"/></svg>Risk Manager</li>
    <li><svg><use href="#icon-arrow"/></svg>Network Defense</li>
    <li><svg><use href="#icon-arrow"/></svg>Policy Framework</li>
    <li><svg><use href="#icon-arrow"/></svg>Dedicated Classes</li>
  </ul>
  <div class="callout">A variety<br>of courses for<br>the security<br>practitioner</div>

  <h2 class="section-title" style="left:518px;top:678px">CONSULTING</h2>
  <ul class="list list-consulting" style="left:518px;top:714px">
    <li><svg><use href="#icon-arrow"/></svg>Guardline Plus (a top tier service)</li>
    <li><svg><use href="#icon-arrow"/></svg><span>Legal Information Security and Protection<span class="note">(our new offering)</span></span></li>
    <li><svg><use href="#icon-arrow"/></svg>Health Information Security and Protection</li>
    <li><svg><use href="#icon-arrow"/></svg>Company Wide Policies and Procedures</li>
    <li><svg><use href="#icon-arrow"/></svg>Security Reviews and Risk Assessments</li>
    <li><svg><use href="#icon-arrow"/></svg><span>General IT Consulting, Management<span class="note">and Outsourcing</span></span></li>
  </ul>

  <h2 class="offer-title">For expo attendees, we are<br>offering a special discount.</h2>
  <ul class="offer-list">
    <li>Our monthly rate is $5000 (one year contract).</li>
    <li>For Expo attendees, we are offering a <span class="highlight">40% discount.</span><span class="rate">Special Expo rate of $3000/month (one year contract).</span></li>
  </ul>

  <div class="brand">
    <div class="brand-mark"></div>
    <div class="brand-name">VANTREL<br>SYSTEMS</div>
  </div>

  <footer class="footer">
    <div class="contact-name">LEON WHITCOMBE</div>
    <div class="contact-role">Chief Security Consultant</div>
    <div class="divider" style="left:277px"></div>
    <div class="phone">
      <svg width="20" height="20" viewBox="0 0 20 20" aria-hidden="true"><circle cx="10" cy="10" r="8.5" fill="none" stroke="#fff" stroke-width="1.6"/><path d="M7 5.5c-1 1-1 3 1 5.5s4.5 3 5.5 2l-1.3-1.6-1.5.7c-1-.6-2-1.8-2.5-2.8l.8-1.4z" fill="#fff"/></svg>
      555-318-7292
    </div>
    <div class="email">
      <svg width="16" height="12" viewBox="0 0 16 12" aria-hidden="true"><rect x="0.5" y="0.5" width="15" height="11" fill="#fff"/><path d="M1 1l7 6 7-6" fill="none" stroke="#58585a" stroke-width="1.4"/></svg>
      leon.whitcombe@vantrelsys.example
    </div>
    <div class="divider" style="left:594px"></div>
    <div class="web">www.vantrelsys.example</div>
  </footer>
</main>
</body>
</html>
```